Kestrada LLC, needs a web page no more than 5 pages (for now)

Kestrada is a general contractor. Our services include general contracting, design-build construction, disaster recovery and environmental remediation. Our main clients are PMX, TQ, State and Local Gov't Agencies, Hospitals and Schools. Kestrada is also a SDVOSB.

```html
<!DOCTYPE html>
<html lang="en">
<head>
<meta charset="utf-8">
<title>Kestrada LLC — General Contractor</title>
<link href="https://fonts.googleapis.com/css2?family=Poppins:wght@400;500;600;700&display=swap" rel="stylesheet">
<style>
:root{
  --gold:#c39a3c;
  --gold-dark:#a98226;
  --ink:#222222;
  --nav:#2b2b2b;
  --footer:#1f1f1f;
  --cream:#f7f3ec;
  --muted:#555555;
  --line:#dddddd;
  --white:#ffffff;
}
*{margin:0;padding:0;box-sizing:border-box}
html,body{width:1200px;height:4629px;overflow:hidden}
body{font-family:"Poppins",sans-serif;color:var(--ink);background:var(--white);position:relative}
.abs{position:absolute}
.btn{position:absolute;display:flex;align-items:center;justify-content:center;background:var(--gold);color:var(--white);font-size:12px;font-weight:600;text-transform:uppercase;letter-spacing:.3px}
.brand{display:flex;align-items:center;gap:8px;font-weight:600;color:var(--gold);letter-spacing:1px}
.brand .dot{width:18px;height:18px;border-radius:50%;background:var(--gold)}
.section-title{position:absolute;left:0;width:1200px;text-align:center;font-size:30px;font-weight:600}

/* header */
.site-header{position:absolute;left:0;top:0;width:1200px;height:79px;background:var(--white)}
.site-header .brand{position:absolute;left:160px;top:26px;font-size:22px}
.call{position:absolute;left:711px;top:20px;display:flex;align-items:center;gap:10px}
.call .ring{width:32px;height:32px;border-radius:50%;border:1px solid var(--gold);display:flex;align-items:center;justify-content:center}
.call small{display:block;font-size:10px;color:var(--muted);line-height:1.2}
.call b{font-size:15px;font-weight:600}
.main-nav{position:absolute;left:0;top:79px;width:1200px;height:43px;background:var(--nav)}
.main-nav a{position:absolute;top:12px;transform:translateX(-50%);color:var(--white);font-size:13px;text-decoration:none}
.main-nav a.active::after{content:"";position:absolute;left:-6px;right:-6px;bottom:-10px;height:2px;background:var(--gold)}

/* hero */
.hero{position:absolute;left:0;top:122px;width:1200px;height:571px}
.hero-photo{position:absolute;inset:0;background:linear-gradient(100deg,#2a241c 0%,#4a3f31 35%,#6d5a3f 60%,#8a6a2e 85%,#a57a22 100%)}
.hero-photo::after{content:"";position:absolute;inset:0;background:rgba(0,0,0,.3)}
.hero h1{position:absolute;left:160px;top:178px;color:var(--white);font-size:40px;line-height:49px;font-weight:600}
.hero p{position:absolute;left:160px;top:290px;color:var(--white);font-size:13px;line-height:15px;width:420px}
.quote-form{position:absolute;left:700px;top:34px;width:338px;height:505px;background:rgba(22,22,22,.88)}
.quote-form header{height:72px;background:var(--white);display:flex;align-items:center;justify-content:space-between;padding:0 22px 0 27px}
.quote-form header h3{font-size:16px;font-weight:600}
.quote-form header .brand{font-size:15px}
.quote-form header .brand .dot{width:14px;height:14px}
.field{position:absolute;left:17px;width:304px;height:44px;background:var(--white);font-size:11px;color:#888;padding:15px 17px}
.field svg{position:absolute;right:16px;top:17px}

/* about */
.about{position:absolute;left:0;top:693px;width:1200px;height:455px;background:#f4f4f4}
.about-photo{position:absolute;left:0;top:0;width:593px;height:455px;background:linear-gradient(160deg,#dfe3e8 0%,#c7ccd3 45%,#9a8c7a 75%,#d27a35 100%)}
.about h2{position:absolute;left:623px;top:106px;font-size:30px;font-weight:600}
.about p{position:absolute;left:623px;top:157px;width:410px;font-size:11.5px;line-height:19.5px;color:#333}

/* services */
.service-card{position:absolute;width:420px}
.service-card .photo{width:420px;height:239px}
.service-card h3{margin-top:18px;font-size:18px;font-weight:600;display:flex;justify-content:space-between;align-items:center}
.service-card p{margin-top:16px;font-size:11.5px;line-height:15px;color:#444;width:390px}

/* cta band */
.cta-band{position:absolute;left:0;top:2058px;width:1200px;height:297px;background:var(--gold)}
.cta-photo{position:absolute;left:490px;top:0;width:710px;height:297px;clip-path:polygon(110px 0,710px 0,710px 297px,0 297px);background:linear-gradient(90deg,#e9e4dc 0%,#cbc3b5 40%,#8e9aa6 70%,#55616d 100%)}
.cta-band h2{position:absolute;left:160px;top:48px;color:var(--white);font-size:26px;line-height:32px;font-weight:600}
.cta-band p{position:absolute;left:160px;top:127px;width:300px;color:var(--white);font-size:11px;line-height:13.5px}

/* clients */
.clients{position:absolute;left:0;top:2355px;width:1200px;height:551px;background:var(--cream)}
.client{position:absolute;display:flex;flex-direction:column;align-items:center;justify-content:flex-end;font-size:13px;font-weight:500;padding-bottom:14px}
.client .seal{width:118px;height:118px;border-radius:50%;background:#1e3466;margin-bottom:20px}
.client.divider{border-right:1px solid var(--line)}

/* projects */
.project{position:absolute;width:266px;text-align:center}
.project .photo{height:282px}
.project h4{margin-top:22px;font-size:14px;font-weight:500}
.project .go{margin:18px auto 0;width:40px;height:40px;border-radius:50%;border:1.5px solid var(--gold);display:flex;align-items:center;justify-content:center}

/* why choose */
.why-bg{position:absolute;left:0;top:3646px;width:1200px;height:329px;background:linear-gradient(180deg,#ffffff 0%,#f0f0ef 45%,#e3e1de 100%)}
.why-item{position:absolute;width:220px;text-align:center}
.why-item .ring{margin:0 auto;width:140px;height:140px;border-radius:50%;border:1.5px dashed var(--gold);background:var(--white);display:flex;align-items:center;justify-content:center}
.why-item h4{margin-top:24px;font-size:14px;font-weight:600;line-height:17px}

/* contact band */
.contact-band{position:absolute;left:0;top:3975px;width:1200px;height:328px;background:var(--gold)}
.contact-photo{position:absolute;left:530px;top:-60px;width:620px;height:388px;background:linear-gradient(160deg,rgba(230,200,120,0) 0%,#b58a33 35%,#7a6a55 65%,#3f3a33 100%)}
.contact-band .kicker{position:absolute;left:160px;top:52px;font-size:12px;color:var(--white)}
.contact-band h2{position:absolute;left:160px;top:88px;font-size:29px;line-height:36px;color:var(--white);font-weight:600}
.contact-band p{position:absolute;left:160px;top:168px;width:426px;font-size:11px;line-height:14px;color:var(--white)}
.contact-band .btn{left:162px;top:240px;width:233px;height:36px;background:#1c1c1c;border-radius:3px}

/* footer */
.site-footer{position:absolute;left:0;top:4303px;width:1200px;height:326px;background:var(--footer);color:var(--white)}
.site-footer .brand{position:absolute;left:190px;top:110px;font-size:24px}
.social{position:absolute;left:176px;top:180px;display:flex;gap:25px}
.social span{width:18px;height:18px;border-radius:50%;border:1.5px solid var(--white)}
.site-footer h5{position:absolute;font-size:16px;font-weight:500}
.site-footer a{position:absolute;color:var(--white);font-size:13px;text-decoration:none}
.contact-line{position:absolute;left:785px;display:flex;gap:14px;font-size:13px;line-height:16px}
.contact-line svg{flex:none;margin-top:1px}
.copyright{position:absolute;left:0;top:4575px;width:1200px;text-align:center;font-size:11px;color:#ccc}
</style>
</head>
<body>

<header class="site-header">
  <div class="brand"><span class="dot"></span>KESTRADA</div>
  <div class="call">
    <span class="ring"><svg width="14" height="14" viewBox="0 0 24 24"><path d="M6.6 10.8a15 15 0 006.6 6.6l2.2-2.2a1 1 0 011-.25 11.4 11.4 0 003.6.6 1 1 0 011 1V20a1 1 0 01-1 1A17 17 0 013 4a1 1 0 011-1h3.5a1 1 0 011 1c0 1.25.2 2.45.6 3.6a1 1 0 01-.25 1z" fill="#c39a3c"/></svg></span>
    <div><small>Call Us</small><b>(555) 014-3820</b></div>
  </div>
  <div class="btn" style="left:892px;top:20px;width:146px;height:38px">Start Free Quote</div>
</header>

<nav class="main-nav">
  <a class="active" style="left:270px">Home</a>
  <a style="left:383px">About</a>
  <a style="left:510px">Services</a>
  <a style="left:639px">Our Clients</a>
  <a style="left:776px">Projects</a>
  <a style="left:911px">Contact Us</a>
</nav>

<section class="hero">
  <div class="hero-photo" role="img" aria-label="Construction site with excavator at dusk"></div>
  <h1>Building with Precision.<br>Serving with Kestrada.</h1>
  <p>General Contracting • Design-Build • Disaster Recovery<br>Environmental Remediation.</p>
  <div class="btn" style="left:162px;top:348px;width:155px;height:38px">Work With Us</div>
  <form class="quote-form">
    <header><h3>Have Question?</h3><div class="brand"><span class="dot"></span>KESTRADA</div></header>
    <div class="field" style="top:92px">Name*</div>
    <div class="field" style="top:153px">Email*</div>
    <div class="field" style="top:215px">Phone*</div>
    <div class="field" style="top:276px">Service*<svg width="14" height="8" viewBox="0 0 14 8"><path d="M1 1l6 6 6-6" stroke="#666" fill="none" stroke-width="1.5"/></svg></div>
    <div class="field" style="top:338px;height:90px">Message*</div>
    <div class="btn" style="left:17px;top:446px;width:304px;height:44px">Submit Now</div>
  </form>
</section>

<section class="about">
  <div class="about-photo" role="img" aria-label="Two engineers in hard hats holding rolled plans"></div>
  <h2>About Us</h2>
  <p>Lorem Ipsum is simply dummy text of the printing and typesetting industry. Lorem Ipsum has been the industry's standard dummy text ever since the 1500s, when an unknown printer took a galley of type and scrambled it to make a type specimen book.<br>Lorem Ipsum is simply dummy text of the printing and typesetting industry. Lorem Ipsum has been the industry's standard dummy specimen book.</p>
  <div class="btn" style="left:623px;top:313px;width:146px;height:38px">Learn More</div>
</section>

<h2 class="section-title" style="top:1200px">Our Services</h2>
<svg width="0" height="0" style="position:absolute"><defs><symbol id="arrow" viewBox="0 0 20 10"><path d="M0 5h18M14 1l4 4-4 4" stroke="#444" fill="none" stroke-width="1.3"/></symbol></defs></svg>

<article class="service-card" style="left:160px;top:1284px">
  <div class="photo" role="img" aria-label="Contractor and engineer reviewing a site" style="background:linear-gradient(135deg,#7b6a55,#c9a86a 55%,#8a8f96)"></div>
  <h3>General Contracting<svg width="20" height="10"><use href="#arrow"/></svg></h3>
  <p>Architectural shingles are the most cost effective choice in roofing, that is why they are common choice...</p>
</article>
<article class="service-card" style="left:618px;top:1284px">
  <div class="photo" role="img" aria-label="Engineers studying building plans outdoors" style="background:linear-gradient(135deg,#9aa1a8,#c8b48a 55%,#e08a3a)"></div>
  <h3>Design-Build Construction<svg width="20" height="10"><use href="#arrow"/></svg></h3>
  <p>Architectural shingles are the most cost effective choice in roofing, that is why they are choice...</p>
</article>
<article class="service-card" style="left:160px;top:1665px">
  <div class="photo" role="img" aria-label="Damaged building after a disaster" style="background:linear-gradient(180deg,#5f7fa8,#9eb0c4 45%,#8b7f72 75%,#5e6b48)"></div>
  <h3>Disaster Recovery<svg width="20" height="10"><use href="#arrow"/></svg></h3>
  <p>Vinyl siding is a great option to give your home's exterior a beautiful makeover...</p>
</article>
<article class="service-card" style="left:618px;top:1665px">
  <div class="photo" role="img" aria-label="Field workers sampling soil in a forest" style="background:linear-gradient(135deg,#3f4a35,#6f7f4f 50%,#c8c15a)"></div>
  <h3>Environmental Remediation<svg width="20" height="10"><use href="#arrow"/></svg></h3>
  <p>Vinyl siding is a great option to give your home's exterior a beautiful makeover...</p>
</article>

<section class="cta-band">
  <div class="cta-photo" role="img" aria-label="Architects working over drawings at a desk"></div>
  <h2>Ready To Start Your<br>Next Project With Kestrada?</h2>
  <p>Started helping people with their home improvement projects. His very first job was installing window trim for a wonderful homeowner in Pine Hollow MN.<br>touch.</p>
  <div class="btn" style="left:162px;top:216px;width:145px;height:38px;background:var(--white);color:var(--gold);font-size:11px">Contact Us</div>
</section>

<section class="clients">
  <h2 class="section-title" style="top:45px;background:none">Our Clients</h2>
  <div class="client divider" style="left:246px;top:132px;width:217px;height:153px"><span class="seal"></span>PMX</div>
  <div class="client divider" style="left:463px;top:132px;width:237px;height:153px"><span class="seal"></span>TQ</div>
  <div class="client" style="left:700px;top:132px;width:255px;height:153px">
    <div style="display:flex;align-items:center;gap:8px;font-size:22px;font-weight:600;color:#1e3466;margin-bottom:40px"><span style="width:22px;height:22px;background:#1e3466"></span>Learnfield Academy</div>Schools</div>
  <div class="client" style="left:246px;top:294px;width:352px;height:183px;border-top:1px solid var(--line)"><span class="seal" style="width:110px;height:110px;background:#2d6a5a"></span><span style="line-height:17px;text-align:center">State and Local<br>Gov't Agencies</span></div>
  <div class="abs" role="img" aria-label="Modern hospital building" style="left:598px;top:294px;width:357px;height:183px;background:linear-gradient(90deg,#ffffff 0%,#eef3f8 40%,#b9cde0 75%,#8fb07a 100%)"></div>
  <div class="abs" style="left:612px;top:380px;font-size:13px;font-weight:500">Hospitals</div>
</section>

<h2 class="section-title" style="top:2958px">Our Projects</h2>
<svg width="0" height="0" style="position:absolute"><defs><symbol id="arrow-gold" viewBox="0 0 16 10"><path d="M0 5h14M10 1l4 4-4 4" stroke="#222" fill="none" stroke-width="1.4"/></symbol></defs></svg>
<div class="project" style="left:31px;top:3050px"><div class="photo" role="img" aria-label="Technician and soldier reviewing a laptop" style="background:linear-gradient(135deg,#2d3e52,#6a87a0 50%,#5a5a3c)"></div><h4>Military / PMX Renovations</h4><div class="go"><svg width="16" height="10"><use href="#arrow-gold"/></svg></div></div>
<div class="project" style="left:321px;top:3050px"><div class="photo" role="img" aria-label="Hospital building under construction with crane" style="background:linear-gradient(180deg,#e9ecef,#b8a68a 60%,#7b6a52)"></div><h4>Hospital Renovations</h4><div class="go"><svg width="16" height="10"><use href="#arrow-gold"/></svg></div></div>
<div class="project" style="left:612px;top:3050px"><div class="photo" role="img" aria-label="Electricians at work in safety vests" style="background:linear-gradient(135deg,#3f4640,#8a8f7a 50%,#d98a3a)"></div><h4>Electrical</h4><div class="go"><svg width="16" height="10"><use href="#arrow-gold"/></svg></div></div>
<div class="project" style="left:903px;top:3050px"><div class="photo" role="img" aria-label="Road paving machine on fresh asphalt" style="background:linear-gradient(160deg,#4f6b6a,#2f3f42 55%,#1d2628)"></div><h4>Roadway</h4><div class="go"><svg width="16" height="10"><use href="#arrow-gold"/></svg></div></div>
<div class="btn" style="left:519px;top:3468px;width:158px;height:38px;font-size:11px">View All Projects</div>

<h2 class="section-title" style="top:3570px">Why Choose Kestrada</h2>
<div class="why-bg" role="img" aria-label="Faint architectural blueprints on a desk"></div>
<div class="why-item" style="left:246px;top:3657px">
  <div class="ring"><svg width="60" height="56" viewBox="0 0 60 56" fill="none" stroke="#c39a3c" stroke-width="2"><circle cx="30" cy="30" r="6"/><circle cx="14" cy="33" r="5"/><circle cx="46" cy="33" r="5"/><path d="M19 54v-6a11 11 0 0122 0v6M4 54v-4a9 9 0 0114 0M42 50a9 9 0 0114 0v4M20 4l2 4 4 .5-3 3 1 4-4-2-4 2 1-4-3-3 4-.5zM40 4l2 4 4 .5-3 3 1 4-4-2-4 2 1-4-3-3 4-.5z"/></svg></div>
  <h4>Veteran-Owned Expertise<br>(SDVOSB)</h4>
</div>
<div class="why-item" style="left:497px;top:3657px">
  <div class="ring"><svg width="50" height="58" viewBox="0 0 50 58" fill="none" stroke="#c39a3c" stroke-width="2"><path d="M4 2h30l10 10v44H4z"/><path d="M11 16h20M11 24h26M11 32h26M11 40h12"/><circle cx="38" cy="46" r="8" fill="#fff"/><path d="M34 46l3 3 5-6"/></svg></div>
  <h4>Government Contracting<br>Experience</h4>
</div>
<div class="why-item" style="left:748px;top:3657px">
  <div class="ring"><svg width="50" height="58" viewBox="0 0 50 58" fill="none" stroke="#c39a3c" stroke-width="2.5"><path d="M25 3l20 8v16c0 13-9 23-20 28C14 50 5 40 5 27V11z"/><path d="M16 29l7 7 12-13"/></svg></div>
  <h4>Precision, Safety, And<br>Compliance</h4>
</div>

<section class="contact-band">
  <div class="contact-photo" role="img" aria-label="Two engineers with plans pointing toward a building"></div>
  <div class="kicker">Contact</div>
  <h2>Ready To Start Your<br>Next Project With Kestrada?</h2>
  <p>Lorem Ipsum is simply dummy text of the printing and typesetting industry. Lorem Ipsum has been the industry's standard dummy text ever since the 1500s, when an unknown printer took a galley of type and scrambled it to make a type specimen book.</p>
  <div class="btn">Contact Us Today</div>
</section>

<footer class="site-footer">
  <div class="brand"><span class="dot"></span>KESTRADA</div>
  <div class="social" aria-label="Social links"><span></span><span></span><span></span><span></span></div>
  <h5 style="left:460px;top:52px">Quick Links</h5>
  <a style="left:460px;top:100px">Home</a>
  <a style="left:460px;top:137px">About Us</a>
  <a style="left:460px;top:175px">Services</a>
  <a style="left:460px;top:213px">Contact Us</a>
  <a style="left:603px;top:100px">Clients</a>
  <a style="left:603px;top:137px">Projects</a>
  <a style="left:603px;top:175px">News</a>
  <h5 style="left:774px;top:52px">Contact Us</h5>
  <div class="contact-line" style="top:100px"><svg width="13" height="13" viewBox="0 0 24 24"><path d="M6.6 10.8a15 15 0 006.6 6.6l2.2-2.2a1 1 0 011-.25 11.4 11.4 0 003.6.6 1 1 0 011 1V20a1 1 0 01-1 1A17 17 0 013 4a1 1 0 011-1h3.5a1 1 0 011 1c0 1.25.2 2.45.6 3.6a1 1 0 01-.25 1z" fill="#fff"/></svg>(555) 014-3820</div>
  <div class="contact-line" style="top:137px"><svg width="13" height="11" viewBox="0 0 24 18"><path d="M1 1h22v16H1z" fill="#fff"/><path d="M1 1l11 9 11-9" stroke="#1f1f1f" stroke-width="2" fill="none"/></svg>info@kestrada-build.com</div>
  <div class="contact-line" style="top:167px"><svg width="12" height="16" viewBox="0 0 16 22"><path d="M8 0a8 8 0 018 8c0 6-8 14-8 14S0 14 0 8a8 8 0 018-8z" fill="#fff"/><circle cx="8" cy="8" r="3" fill="#1f1f1f"/></svg><span>48 Alder Crossing Suite 4<br>Millbrook, WI 53999 USA</span></div>
</footer>
<div class="copyright">© 2025 Copyright - kestrada</div>

</body>
</html>
```